Business Card Design for Property Development Company Director

I am looking for a professional and unforgettable business card design for our Director of our Property Development Company.
Please see attached .pptx file to find out what information to include. You don't have to follow the exact format shown in the file - I am interested to see your creative flair using the information provided.

```html
<!DOCTYPE html>
<html lang="en">
<head>
<meta charset="utf-8">
<title>Halvern Property Group – Business Card</title>
<link href="https://fonts.googleapis.com/css2?family=Roboto:wght@400;500;700&family=Roboto+Condensed:wght@700&display=swap" rel="stylesheet">
<style>
  :root {
    --bg: #e4e5e7;
    --card: #f4f4f4;
    --blue: #22468f;
    --blue-dark: #1d3c7c;
    --grey: #56585c;
    --grey-mid: #6b6d71;
    --white: #ffffff;
  }
  * { margin: 0; padding: 0; box-sizing: border-box; }
  html, body { width: 1200px; height: 726px; overflow: hidden; }
  body {
    background: var(--bg);
    font-family: "Roboto", Arial, sans-serif;
    position: relative;
  }
  .card {
    position: absolute;
    top: 211px;
    width: 530px;
    height: 303px;
    background: var(--card);
    box-shadow: 0 10px 24px rgba(0,0,0,0.18);
    overflow: hidden;
  }
  .card--front { left: 45px; }
  .card--back { left: 625px; }

  /* Front */
  .tagline {
    position: absolute;
    top: 34px; left: 0; right: 0;
    text-align: center;
    color: var(--blue);
    font-size: 19px;
    line-height: 1.2;
  }
  .brand {
    position: absolute;
    top: 110px; left: 0; right: 0;
    display: flex;
    justify-content: center;
    align-items: center;
    gap: 14px;
  }
  .brand__mark {
    width: 46px; height: 46px;
    background: var(--grey);
  }
  .brand__name {
    color: var(--blue);
    font-weight: 700;
    font-size: 34px;
    letter-spacing: 1px;
    line-height: 1.05;
  }
  .brand__name small {
    display: block;
    font-size: 17px;
    letter-spacing: 5px;
  }
  .invite {
    position: absolute;
    top: 200px; left: 0; right: 0;
    text-align: center;
    color: var(--grey);
    font-size: 14.5px;
  }
  .invite strong { color: var(--blue); font-weight: 400; }
  .band {
    position: absolute;
    left: 0; right: 0; top: 236px;
    height: 14px;
    display: flex;
  }
  .band__grey { width: 44%; background: var(--grey-mid); }
  .band__blue { flex: 1; background: var(--blue); }

  /* Back */
  .back-shape { position: absolute; inset: 0; }
  .person {
    position: absolute;
    top: 42px; left: 38px;
    color: var(--white);
  }
  .person__name {
    font-family: "Roboto Condensed", "Arial Narrow", sans-serif;
    font-weight: 700;
    font-size: 21px;
  }
  .person__role { font-size: 13px; margin-top: 4px; opacity: 0.9; }
  .contacts {
    position: absolute;
    left: 38px; bottom: 36px;
    list-style: none;
    color: var(--white);
    font-size: 14px;
    line-height: 1.45;
  }
  .contacts li { display: flex; align-items: center; gap: 10px; }
  .contacts svg { width: 13px; height: 13px; flex: none; }
  .contacts .licence { display: block; margin-top: 4px; padding-left: 0; }
  .back-brand {
    position: absolute;
    top: 150px; left: 452px;
    transform: translate(-50%, -50%) rotate(-90deg);
    display: flex; align-items: center; gap: 10px;
    white-space: nowrap;
  }
  .back-brand .brand__name { font-size: 30px; }
  .back-brand .brand__name small { font-size: 15px; letter-spacing: 4px; }
  .back-brand .brand__mark { width: 38px; height: 38px; }
</style>
</head>
<body>
  <section class="card card--front">
    <p class="tagline">Property Development<br>&amp; Site Acquisition Specialists</p>
    <div class="brand">
      <span class="brand__mark"></span>
      <span class="brand__name">HALVERN<small>PROPERTY GROUP</small></span>
    </div>
    <p class="invite">Ask me about our <strong>INVESTMENT &amp; PARTNERSHIP</strong> opportunities</p>
    <div class="band"><span class="band__grey"></span><span class="band__blue"></span></div>
  </section>

  <section class="card card--back">
    <svg class="back-shape" viewBox="0 0 530 303" width="530" height="303" aria-hidden="true">
      <rect width="530" height="303" fill="var(--blue)"/>
      <path d="M300 0 Q 425 120 448 303 L530 303 L530 0 Z" fill="var(--grey-mid)"/>
      <path d="M312 0 Q 437 120 460 303 L530 303 L530 0 Z" fill="var(--card)"/>
    </svg>
    <div class="person">
      <p class="person__name">Daniel Mercer</p>
      <p class="person__role">Director</p>
    </div>
    <ul class="contacts">
      <li>
        <svg viewBox="0 0 16 16"><path d="M4 1l3 3-2 2c1 2 3 4 5 5l2-2 3 3-2 3C7 15 1 9 1 3z" fill="#fff"/></svg>
        0400 318 726
      </li>
      <li>
        <svg viewBox="0 0 16 16"><rect x="1" y="3" width="14" height="10" fill="none" stroke="#fff" stroke-width="1.6"/><path d="M1 3l7 6 7-6" fill="none" stroke="#fff" stroke-width="1.6"/></svg>
        daniel@halvern.com.au
      </li>
      <li>
        <svg viewBox="0 0 16 16"><circle cx="8" cy="8" r="6.5" fill="none" stroke="#fff" stroke-width="1.5"/><path d="M1.5 8h13M8 1.5c-3 3.5-3 9.5 0 13M8 1.5c3 3.5 3 9.5 0 13" fill="none" stroke="#fff" stroke-width="1.2"/></svg>
        www.halvern.com.au
      </li>
      <li class="licence">Real Estate Lic:<br>5172093 &amp; 5172094</li>
    </ul>
    <div class="back-brand">
      <span class="brand__mark"></span>
      <span class="brand__name">HALVERN<small>PROPERTY GROUP</small></span>
    </div>
  </section>
</body>
</html>
```